Verlindo Magician

I want the business card for my business to give to people who watch that later I will be employed to show magic here is my website http://www.balsamomagicien.com/I want the interesting design , i am very opened for formal and informal, I watch a lot of design so don't stick to the common shape and form but i hope it can also be produced the thing to write on will be the same as in picture that i will upload , i also will upload the logo for you that so can be easy to useDenis CostilleMagicianMAGICIAN VERLINDO 17 rue des Tilleuls - 25000 BESANÇON contact@verlindoillusions.example tel. 0381 946 157 tel. 0674 219 503

```html
<!DOCTYPE html>
<html lang="fr">
<head>
<meta charset="utf-8">
<title>Verlindo Magician – Business Card</title>
<link href="https://fonts.googleapis.com/css2?family=Jost:wght@400&display=swap" rel="stylesheet">
<style>
  :root {
    --backdrop: #dcdcdc;
    --card: #ffffff;
    --ink: #141414;
    --ink-soft: #555555;
    --accent: #e3262b;
    --placeholder: #e4e4e4;
  }
  * { margin: 0; padding: 0; box-sizing: border-box; }
  html, body {
    width: 1125px;
    height: 1200px;
    overflow: hidden;
    background: var(--backdrop);
    font-family: "Jost", "Futura", sans-serif;
  }
  .card {
    position: absolute;
    left: 171px;
    width: 825px;
    height: 471px;
    background: var(--card);
    box-shadow: 0 2px 6px rgba(0,0,0,0.18);
  }
  .card--front { top: 106px; }
  .card--back  { top: 639px; }

  .holder {
    position: absolute;
    top: 46px;
    right: 46px;
    text-align: right;
    line-height: 1;
  }
  .holder__name {
    font-size: 31px;
    color: var(--ink);
    letter-spacing: 0.2px;
  }
  .holder__role {
    margin-top: 3px;
    font-size: 22px;
    color: var(--accent);
  }

  .contact {
    position: absolute;
    left: 48px;
    top: 339px;
    font-size: 19.5px;
    font-style: normal;
    color: var(--ink-soft);
    line-height: 1;
  }
  .contact__line { display: block; white-space: nowrap; }
  .contact__line + .contact__line { margin-top: 8px; }
  .contact__line--address { margin-top: 14px !important; }
  .contact__label { color: var(--accent); }
  .contact__sep { margin: 0 3px; }

  .brand-mark {
    position: absolute;
    left: 297px;
    top: 80px;
    width: 230px;
    height: 230px;
    background: var(--placeholder);
  }
  .brand {
    position: absolute;
    left: 0;
    right: 0;
    top: 343px;
    text-align center;
    text-align: center;
    font-size: 43px;
    color: var(--ink);
    letter-spacing: 1px;
    line-height: 1;
  }
</style>
</head>
<body>

  <section class="card card--front">
    <header class="holder">
      <p class="holder__name">MARC RAVOULET</p>
      <p class="holder__role">MAGICIAN</p>
    </header>

    <address class="contact">
      <span class="contact__line">
        <span class="contact__label">T.</span> 0381 946 157
        <span class="contact__label">P.</span> 0674 219 503
      </span>
      <span class="contact__line">
        contact@verlindoillusions.example<span class="contact__sep">|</span>www.verlindoillusions.example
      </span>
      <span class="contact__line contact__line--address">
        <span class="contact__label">MAGICIAN VERLINDO</span> 17 rue des Tilleuls - 25000 BESANÇON
      </span>
    </address>
  </section>

  <section class="card card--back">
    <div class="brand-mark" role="img" aria-label="Brand emblem area"></div>
    <p class="brand">VERLINDO</p>
  </section>

</body>
</html>
```